PHD-project

i need the figures to be in the same stile. info is inside the file. There are 5 figures that need redesign. this is for PhD.

Target Market(s)

it will be used in my phd

Colors

```html
<!DOCTYPE html>
<html lang="en">
<head>
<meta charset="utf-8">
<title>PhD Research Overview</title>
<link rel="stylesheet" href="https://fonts.googleapis.com/css2?family=Roboto:wght@300;400&display=swap">
<style>
  :root {
    --frame: #2e3a8f;
    --ink: #1b1b1b;
    --sky-light: #aee0f4;
    --sky-mid: #8cbde3;
    --practice: #6cbde9;
    --deep: #1a587a;
    --cap: #2a86b8;
    --triangle: #98d3f0;
    --arrow: #e0262b;
    --box-edge: #978eae;
    --findings-edge: #1f72c4;
    --on-deep: #cfe9f7;
  }
  html, body {
    margin: 0;
    padding: 0;
    width: 1200px;
    height: 1200px;
    overflow: hidden;
    background: #ffffff;
  }
  .overview {
    display: block;
    width: 1200px;
    height: 1200px;
    font-family: "Roboto", Arial, sans-serif;
  }
  .section-title { font-size: 20px; font-weight: 300; fill: var(--ink); letter-spacing: 0.3px; }
  .label { font-size: 14px; font-weight: 300; fill: var(--ink); }
  .label-light { font-size: 14px; font-weight: 300; fill: var(--on-deep); }
  .cap-label { font-size: 20px; font-weight: 300; fill: #0f2a3a; }
  .rtd-title { font-size: 27px; font-weight: 300; fill: var(--ink); }
  .frame { fill: none; stroke: var(--frame); stroke-width: 6; }
  .brace { fill: none; stroke: var(--deep); stroke-width: 5; }
  .triangle { fill: var(--triangle); }
  .bullet { fill: var(--deep); }
  .bullet-faint { fill: #2e7aa3; }
  .column-box { stroke: var(--box-edge); stroke-width: 5; fill: url(#boxGradient); }
  .findings-box { stroke: var(--findings-edge); stroke-width: 5; fill: var(--deep); }
  .arrow-outline { fill: #ffffff; stroke: var(--arrow); stroke-width: 2; }
  .arrow-bar { fill: var(--arrow); }
</style>
</head>
<body>
<svg class="overview" viewBox="0 0 1500 1500" xmlns="http://www.w3.org/2000/svg">
  <defs>
    <linearGradient id="bubbleGradient" x1="0" y1="0" x2="1" y2="0">
      <stop offset="0" stop-color="#b2e2f5"/>
      <stop offset="0.55" stop-color="#a4d6f0"/>
      <stop offset="1" stop-color="#85b2dd"/>
    </linearGradient>
    <linearGradient id="boxGradient" x1="0" y1="0" x2="1" y2="0">
      <stop offset="0" stop-color="#b3e3f6"/>
      <stop offset="0.5" stop-color="#a2d8f1"/>
      <stop offset="1" stop-color="#8ab9e0"/>
    </linearGradient>
  </defs>

  <rect class="frame" x="114" y="426" width="1320" height="726"/>

  <!-- Positioning -->
  <text class="section-title" x="155" y="528">POSITIONING THE RESEARCH</text>
  <ellipse cx="296" cy="925" rx="89" ry="148" fill="url(#bubbleGradient)"/>
  <ellipse cx="295" cy="680" rx="72" ry="120" fill="url(#bubbleGradient)"/>
  <ellipse cx="295" cy="750" rx="46" ry="75" fill="var(--practice)"/>
  <ellipse cx="296" cy="868" rx="56" ry="94" fill="var(--deep)"/>
  <circle cx="294" cy="800" r="27" fill="var(--cap)"/>

  <g class="label" text-anchor="middle">
    <text x="290" y="626">Desing</text>
    <text x="292" y="643">thinking</text>
    <text x="293" y="731">Design</text>
    <text x="296" y="748">practice</text>
    <text x="299" y="988">Design thinking</text>
    <text x="297" y="1005">in organization</text>
  </g>
  <text class="cap-label" x="294" y="810" text-anchor="middle">CAP</text>
  <g class="label-light" text-anchor="middle">
    <text x="296" y="856">Theoretical</text>
    <text x="296" y="873">approach to</text>
    <text x="296" y="890">building design</text>
    <text x="296" y="908">thinking</text>
    <text x="296" y="925">capability</text>
  </g>

  <!-- Research approach -->
  <text class="section-title" x="454" y="528">RESEARCH APPROACH</text>
  <text class="rtd-title" x="553" y="696" text-anchor="middle">RtD</text>
  <text class="label" x="545" y="719" text-anchor="middle">Learning dimension</text>
  <text class="label" x="545" y="736" text-anchor="middle">Pragmatic dimension</text>

  <path class="arrow-outline" d="M389 757 L410 743 L410 750 L694 750 L694 743 L715 757 L694 771 L694 764 L410 764 L410 771 Z"/>
  <rect class="arrow-bar" x="420" y="752" width="262" height="8"/>

  <polygon class="triangle" points="386,780 554,780 470,850"/>
  <polygon class="triangle" points="554,780 722,780 638,850"/>
  <polygon class="triangle" points="471,852 640,852 557,922"/>
  <g class="label" text-anchor="middle">
    <text x="470" y="805">Design practice</text>
    <text x="636" y="805">Design studies</text>
    <text x="553" y="872">Design</text>
    <text x="554" y="889">exploration</text>
  </g>

  <path class="brace" d="M732 504 C752 512 748 540 748 580 L748 740 C748 772 760 786 790 791 C760 796 748 810 748 842 L748 1002 C748 1042 752 1070 732 1078"/>

  <!-- Methods -->
  <text class="section-title" x="895" y="619" text-anchor="middle">METHODS</text>
  <rect class="column-box" x="826" y="635" width="154" height="325" rx="30"/>
  <g class="bullet">
    <polygon points="830,679 838,688 830,697"/>
    <polygon points="830,714 838,723 830,732"/>
    <polygon points="830,749 838,758 830,767"/>
    <polygon points="830,835 838,844 830,853"/>
    <polygon points="830,870 838,879 830,888"/>
    <polygon points="830,905 838,914 830,923"/>
  </g>
  <g class="label">
    <text x="840" y="693">Interventions design</text>
    <text x="840" y="728">Reflection on action</text>
    <text x="840" y="763">Reflective</text>
    <text x="840" y="780">conversation with</text>
    <text x="840" y="797">the situation</text>
    <text x="840" y="815">(reflection in action)</text>
    <text x="840" y="850">Proto- practices</text>
    <text x="840" y="885">Interviews</text>
    <text x="840" y="919">Observations</text>
  </g>

  <!-- Findings -->
  <text class="section-title" x="1102" y="619" text-anchor="middle">FINDINGS</text>
  <rect class="findings-box" x="1027" y="635" width="155" height="325" rx="30"/>
  <g class="bullet-faint">
    <polygon points="1032,665 1040,674 1032,683"/>
    <polygon points="1032,735 1040,744 1032,753"/>
    <polygon points="1032,821 1040,830 1032,839"/>
    <polygon points="1032,873 1040,882 1032,891"/>
  </g>
  <g class="label-light">
    <text x="1045" y="679">The value of semi</text>
    <text x="1045" y="696">structured tools for</text>
    <text x="1045" y="713">non-designers</text>
    <text x="1045" y="749">Openness as a type</text>
    <text x="1045" y="766">of mindset</text>
    <text x="1045" y="783">supporting</text>
    <text x="1045" y="800">competence building</text>
    <text x="1045" y="835">The importance of</text>
    <text x="1048" y="852">insiders / experts</text>
    <text x="1045" y="887">The role of time</text>
    <text x="1045" y="904">during and between</text>
    <text x="1045" y="922">designs activates</text>
  </g>

  <!-- Contribution -->
  <text class="section-title" x="1299" y="621" text-anchor="middle">CONTRIBUTION</text>
  <rect class="column-box" x="1228" y="635" width="153" height="325" rx="30"/>
  <g class="bullet">
    <polygon points="1231,696 1239,705 1231,714"/>
    <polygon points="1231,766 1239,775 1231,784"/>
    <polygon points="1231,870 1239,879 1231,888"/>
  </g>
  <g class="label">
    <text x="1242" y="710">Semi-structured and</text>
    <text x="1242" y="727">visual design tools</text>
    <text x="1242" y="745">(paper 1-4)</text>
    <text x="1242" y="780">Framework of 3 core</text>
    <text x="1242" y="797">concepts dialogical</text>
    <text x="1242" y="814">space (paper 6)</text>
    <text x="1242" y="832">Temporality (paper 6)</text>
    <text x="1242" y="849">Openness (paper5)</text>
    <text x="1242" y="884">Guidelines (paper7)</text>
  </g>
</svg>
</body>
</html>
```